Audio Visual company needs WordPress Site re-design

We need a new, simple and sleek redesign of our website, www.kelvarosupply.net. It is crucial that it is mobile platform friendly! The company emphasis is on commercial sound and video installation.

Examples of what our company does can be found here: http://bramwickav.org/

I am NOT looking for a storefront or an e-commerce site. I would just like an elegant site that describes our services. Perhaps incorporate a sleek showcase into the homepage of projects we have completed. Also would like an elegant menu-bar, perhaps enhance our current site menu or similar.

Here is a link to another site that exhibits the content I am looking for. Their target market is also much like mine.
http://www.pollanderhouse.com/ ........ A polished up version of this site would probably be my ideal site. It has almost EXACTLY the content I am looking for. Exclude the "Printing & signage" category. Needs nicer menus, contact page and project showcase.

Here is another example: http://www.clearhavenmedia.com/ ......... This site has a very nice homepage design with a good layout and feature slider. The site is simple, elegant and to the point.

Target Market(s)

Corporate/commercial business, Educational institutions

Industry/Entity Type

E-Commerce

Font styles to use
Serif
Sans Serif

Requirements
Must have
• Mobile friendly navigation
Nice to have
• HTML5 & CSS3
Should not have
• No Adobe Flash content. No store templates or e-commerce. We are a service based company not a product sales company

```html
<!DOCTYPE html>
<html lang="en">
<head>
<meta charset="utf-8">
<title>Kelvaro Supply — Sound &amp; Video Solutions</title>
<link href="https://fonts.googleapis.com/css2?family=Raleway:wght@400;500;600;700&family=Ubuntu:wght@400;500&display=swap" rel="stylesheet">
<style>
  :root{
    --navy:#0c2570;
    --navy-deep:#0a1f5e;
    --red:#c3161f;
    --blue-text:#1d3f96;
    --ink:#3a3a3a;
    --muted:#555;
    --topbar:#f1f1f1;
    --rule:#dcdcdc;
    --card-border:#e3e3e3;
    --star:#f0a22b;
  }
  *{box-sizing:border-box;margin:0;padding:0}
  html,body{width:852px;height:1200px;overflow:hidden;background:#fff}
  body{font-family:"Ubuntu",sans-serif;color:var(--ink)}
  .page{position:relative;width:852px;height:1200px;overflow:hidden}
  .abs{position:absolute}

  .topbar{left:0;top:0;width:852px;height:34px;background:var(--topbar);font-size:9.5px;color:#666}
  .topbar .item{position:absolute;top:12px;display:flex;align-items:center;gap:6px}

  .brand{left:93px;top:60px;display:flex;align-items:center;gap:8px;font-family:"Raleway",sans-serif;font-weight:700;font-size:24px;color:var(--navy);letter-spacing:.5px}
  .brand .mark{width:14px;height:14px;background:var(--red)}
  .follow{left:653px;top:57px;font-family:"Raleway",sans-serif;font-size:10px;color:#555}
  .social{left:654px;top:78px;display:flex;gap:5px}
  .social span{width:22px;height:22px;border-radius:50%;display:block}

  .nav{left:0;top:121px;width:852px;height:40px;background:var(--navy)}
  .nav a{position:absolute;top:0;height:40px;line-height:40px;font-family:"Raleway",sans-serif;font-weight:500;font-size:10px;color:#fff;text-decoration:none;letter-spacing:.2px}
  .nav a.active{background:var(--red);width:87px;text-align:center}

  .hero{left:0;top:161px;width:852px;height:316px;background:radial-gradient(ellipse at 65% 30%,#1d6f93 0%,#0e3a52 40%,#061a26 75%),#0b2a3a}
  .hero-photo{position:absolute;inset:0;background:linear-gradient(170deg,rgba(0,0,0,.55) 0%,rgba(0,0,0,0) 35%,rgba(20,150,200,.45) 70%,rgba(40,180,220,.55) 100%)}
  .hero-copy{position:absolute;left:124px;top:92px;color:#fff;font-family:"Raleway",sans-serif;font-size:32px;line-height:42px}
  .hero-copy strong{font-weight:700}
  .hero-arrow{position:absolute;top:148px}

  .section-title{left:0;width:852px;text-align:center;font-family:"Raleway",sans-serif;font-size:22px;color:#333;font-weight:400}
  .section-title b{font-weight:700}
  .section-title .accent{color:var(--navy);font-weight:500}
  .intro{left:100px;top:561px;width:652px;text-align:center;font-size:9.4px;line-height:17px;color:var(--muted)}
  .btn{left:387px;top:626px;width:84px;height:29px;background:var(--navy-deep);border-bottom:2px solid #08184a;color:#fff;font-family:"Raleway",sans-serif;font-weight:500;font-size:10px;text-align:center;line-height:28px}
  .rule{left:93px;width:667px;height:1px;background:var(--rule)}
  .subtitle{left:0;width:852px;text-align:center;font-size:9.3px;color:#555}

  .shot{top:765px;width:205px;height:118px;border:3px solid #ececec;box-shadow:0 0 0 1px #e0e0e0}
  .side-btn{top:810px;width:18px;height:34px;background:#e6e6e6;display:flex;align-items:center;justify-content:center}

  .review{top:989px;width:320px;height:113px;border:1px solid var(--card-border);box-shadow:inset 0 0 14px rgba(0,0,0,.04)}
  .review .avatar{position:absolute;left:13px;top:17px;width:37px;height:37px;border-radius:50%;background:linear-gradient(#8a8a8a,#4d4d4d)}
  .review h3{position:absolute;left:62px;top:16px;font-family:"Raleway",sans-serif;font-weight:500;font-size:13.5px;color:var(--blue-text);display:flex;align-items:center;gap:10px;white-space:nowrap}
  .review h3 .stars{font-size:11px;color:var(--star);letter-spacing:1px}
  .review p{position:absolute;left:62px;top:36px;width:250px;font-family:"Raleway",sans-serif;font-size:10.2px;line-height:17px;color:#555}
  .review .meta{position:absolute;left:62px;top:82px;display:flex;gap:12px;font-size:8.5px;color:#444}
  .review .meta span{display:flex;align-items:center;gap:4px}

  .footer{left:0;top:1131px;width:852px;height:69px;background:var(--navy-deep)}
  .footer .copy{position:absolute;left:95px;top:34px;font-family:"Raleway",sans-serif;font-size:9.5px;color:#fff}
  .footer .to-top{position:absolute;left:741px;top:28px}
</style>
</head>
<body>
<div class="page">

  <div class="abs topbar">
    <div class="item" style="left:93px">
      <svg width="9" height="9" viewBox="0 0 10 10"><rect width="10" height="10" rx="1.5" fill="#666"/><path d="M3 2.5c0 3 1.5 4.5 4.5 4.5l.5-1.2-1.2-.7-.6.6c-.9-.4-1.5-1-1.9-1.9l.6-.6-.7-1.2z" fill="#f1f1f1"/></svg>
      (555) 014-2287
    </div>
    <div class="item" style="left:193px">
      <svg width="10" height="8" viewBox="0 0 10 8"><rect width="10" height="8" fill="#666"/><path d="M0 0l5 4 5-4" stroke="#f1f1f1" fill="none"/></svg>
      info@kelvarosupply.net
    </div>
  </div>

  <div class="abs brand"><span class="mark"></span>Kelvaro Supply</div>
  <div class="abs follow">Follow Us</div>
  <div class="abs social">
    <span style="background:#1d4f9c"></span>
    <span style="background:#2a9fd8"></span>
    <span style="background:#f39a1d"></span>
    <span style="background:#c6372c"></span>
  </div>

  <nav class="abs nav">
    <a class="active" href="#" style="left:93px">HOME</a>
    <a href="#" style="left:223px">SERVICES</a>
    <a href="#" style="left:322px">ABOUT US</a>
    <a href="#" style="left:428px">CONTACT US</a>
    <a href="#" style="left:532px">CUSTOMER REVIEWS</a>
  </nav>

  <section class="abs hero" role="img" aria-label="Close-up of a blue-lit audio mixing console with headphones resting on it">
    <div class="hero-photo"></div>
    <div class="hero-copy">Customizing<br><strong>Audio and Video</strong><br>products</div>
    <svg class="hero-arrow" style="left:72px" width="12" height="20" viewBox="0 0 12 20"><path d="M10 2L3 10l7 8" stroke="#bbb" stroke-width="3" fill="none"/></svg>
    <svg class="hero-arrow" style="left:773px" width="12" height="20" viewBox="0 0 12 20"><path d="M2 2l7 8-7 8" stroke="#bbb" stroke-width="3" fill="none"/></svg>
  </section>

  <h1 class="abs section-title" style="top:517px">Welcome to <b>Kelvaro Supply</b></h1>
  <p class="abs intro">Kelvaro Supply has been customizing audio and video products for home and business customers since 2007. We specialize in the design and installation of residential &amp; commercial sound systems, HD video displays, digital projection &amp; digital signage. We are located in Halden Park, a northwest suburb just outside of Brennport. Need an estimate? We will come to you! All of our estimates are done at your home.</p>
  <div class="abs btn">Read More</div>

  <div class="abs rule" style="top:677px"></div>

  <h2 class="abs section-title" style="top:701px">Installations <span class="accent">Gallery</span></h2>
  <p class="abs subtitle" style="top:735px">Neque porro quisquam est qui dolorem ipsum quia dolor sit amet, consectetur, adipisci velit</p>

  <div class="abs side-btn" style="left:0"><svg width="6" height="10" viewBox="0 0 6 10"><path d="M5 1L1 5l4 4" stroke="#555" fill="none" stroke-width="1.5"/></svg></div>
  <div class="abs shot" style="left:93px;background:linear-gradient(135deg,#6a3a2a,#4d9a3a 45%,#c7d84a 60%,#3b2a22)" role="img" aria-label="Wall-mounted screen showing a game graphic in a venue"></div>
  <div class="abs shot" style="left:323px;background:linear-gradient(180deg,#3a2b24 0%,#7a5a3e 35%,#a4643d 60%,#3e2b22 100%)" role="img" aria-label="Row of digital menu boards above a restaurant counter"></div>
  <div class="abs shot" style="left:554px;background:linear-gradient(180deg,#8c8c90,#2a63c8 35%,#1e55c0 70%,#6b6b70)" role="img" aria-label="Two large display screens mounted side by side in a meeting room"></div>
  <div class="abs side-btn" style="left:834px"><svg width="6" height="10" viewBox="0 0 6 10"><path d="M1 1l4 4-4 4" stroke="#555" fill="none" stroke-width="1.5"/></svg></div>

  <div class="abs rule" style="top:913px"></div>

  <h2 class="abs section-title" style="top:946px">Customer Reviews</h2>

  <article class="abs review" style="left:93px">
    <div class="avatar" role="img" aria-label="Customer portrait"></div>
    <h3>Duis aute irure dolor <span class="stars">★★★★☆</span></h3>
    <p>reprehenderit in voluptate velit esse cillum dolore eu fugiat nulla pariatur epteur sint occaec.</p>
    <div class="meta">
      <span><svg width="9" height="9" viewBox="0 0 10 10"><rect x=".5" y="1.5" width="9" height="8" fill="none" stroke="#555"/><path d="M.5 4h9" stroke="#555"/></svg>March 14, 2014</span>
      <span><svg width="9" height="9" viewBox="0 0 10 10"><circle cx="5" cy="5" r="4" fill="none" stroke="#555" stroke-width="1.3"/><path d="M5 2.5V5h2" stroke="#555" fill="none"/></svg>8:28 PM</span>
    </div>
  </article>

  <article class="abs review" style="left:438px">
    <div class="avatar" role="img" aria-label="Customer portrait"></div>
    <h3>Duis aute irure dolor <span class="stars">★★★★☆</span></h3>
    <p>reprehenderit in voluptate velit esse cillum dolore eu fugiat nulla pariatur epteur sint occaec.</p>
    <div class="meta">
      <span><svg width="9" height="9" viewBox="0 0 10 10"><rect x=".5" y="1.5" width="9" height="8" fill="none" stroke="#555"/><path d="M.5 4h9" stroke="#555"/></svg>March 14, 2014</span>
      <span><svg width="9" height="9" viewBox="0 0 10 10"><circle cx="5" cy="5" r="4" fill="none" stroke="#555" stroke-width="1.3"/><path d="M5 2.5V5h2" stroke="#555" fill="none"/></svg>8:28 PM</span>
    </div>
  </article>

  <footer class="abs footer">
    <div class="copy">Copyright ©2014. Yoursite. All Right Reserved</div>
    <svg class="to-top" width="18" height="18" viewBox="0 0 18 18"><circle cx="9" cy="9" r="9" fill="#fff"/><path d="M4.5 11L9 6.5l4.5 4.5" stroke="#0a1f5e" stroke-width="2.4" fill="none"/></svg>
  </footer>

</div>
</body>
</html>
```